Design a modern, classy & professional business card for an online real estate agency, specializing in medium-luxury properties in Thailand and later in Singapore and UK.

Possible design ideas so far: (not essential)

- curved corner(s) to the card, white on front & turquoise on back or visa versa.

- front of card - clear and simple, company name in metallic grey/monochrome, logo graphic & company name on front in spot UV or embossed/debossed effect.

- back of card - large, close-cropped, 'ghost' patterns of the C-shaped curves of logo, or company name repeated on back of card in spot UV.

Target Market(s)

- young to middle-aged professionals mainly (but ideally should design should suit all)

- UK, US,EU,AUS & ASIAN mainly (but ideally should design should suit all countries)

Industry/Entity Type

Real Estate

Requirements
Must have
• THEME:
- Luxurious & Modern
- Clean & striking
- Unique & creative

INFO:
- Logo & company name on front
- Contact details on back:

Tobias Hennlund
Managing Director

www.velmontestates.asia
www.velmontestates.co.uk

Tel: 083-274-6159
email: tobias@velmontestates.asia

(contact details can be displayed in any order as suites design.)

Nice to have
• - curved corner(s) to the card, white on front & turquoise on back or visa versa.

Should not have
• - No generic images of properties, palm trees/coconut trees etc.

- No other other bold colors, except for main turquoise, grey, metallic white & black theme.

- No obvious business card templates

```html
<!DOCTYPE html>
<html lang="en">
<head>
<meta charset="utf-8">
<title>Velmont Estates — Business Card</title>
<link rel="stylesheet" href="https://fonts.googleapis.com/css2?family=Cormorant+Garamond:wght@500&family=Montserrat:ital,wght@0,400;0,700;1,400&display=swap">
<style>
  :root {
    --backdrop: #e9eaeb;
    --turquoise: #74c2bc;
    --turquoise-deep: #66b5ae;
    --logo-grey: #6f6f6f;
    --ink: #2f3b3a;
    --paper: #ffffff;
  }
  * { box-sizing: border-box; margin: 0; padding: 0; }
  html, body { width: 1200px; height: 675px; overflow: hidden; }
  body {
    background: var(--backdrop);
    display: flex;
    align-items: center;
    justify-content: center;
    gap: 44px;
    font-family: "Montserrat", Arial, sans-serif;
  }
  .card {
    position: relative;
    width: 522px;
    height: 298px;
    background: var(--turquoise);
    border-radius: 4px;
    box-shadow: 0 10px 26px rgba(0,0,0,0.12);
    overflow: hidden;
  }
  .card--back { background: var(--turquoise-deep); }

  .brand { display: flex; align-items: center; gap: 16px; }
  .brand__mark { background: var(--paper); flex: none; }
  .brand__name {
    font-family: "Cormorant Garamond", Georgia, serif;
    font-weight: 500;
    color: var(--logo-grey);
    line-height: 1;
    white-space: nowrap;
  }

  .card--front .brand {
    position: absolute; left: 50%; top: 50%;
    transform: translate(-50%, -50%);
  }
  .card--front .brand__mark { width: 92px; height: 92px; }
  .card--front .brand__name { font-size: 46px; }

  .card--back .brand { position: absolute; left: 38px; top: 58px; gap: 12px; }
  .card--back .brand__mark { width: 70px; height: 70px; }
  .card--back .brand__name { font-size: 34px; }

  .contact {
    position: absolute; left: 300px; top: 144px;
    list-style: none;
    font-size: 11.5px;
    color: var(--ink);
  }
  .contact__item { display: flex; align-items: center; gap: 8px; height: 20px; }
  .contact__icon { width: 12px; height: 12px; flex: none; fill: none; stroke: var(--ink); stroke-width: 1.4; }
  .contact__domain { color: var(--paper); }

  .person { position: absolute; left: 182px; top: 226px; }
  .person__name { font-weight: 700; font-size: 14px; color: var(--paper); }
  .person__role { font-style: italic; font-size: 12px; color: var(--ink); margin-top: 2px; }
</style>
</head>
<body>
  <section class="card card--front" aria-label="Card front">
    <div class="brand">
      <div class="brand__mark"></div>
      <span class="brand__name">Velmont Estates</span>
    </div>
  </section>

  <section class="card card--back" aria-label="Card back">
    <div class="brand">
      <div class="brand__mark"></div>
      <span class="brand__name">Velmont Estates</span>
    </div>

    <ul class="contact">
      <li class="contact__item">
        <svg class="contact__icon" viewBox="0 0 12 12"><path d="M2 1.5h2.2l1 2.6-1.4 1a6 6 0 0 0 3.1 3.1l1-1.4 2.6 1V10a1 1 0 0 1-1 1A9.5 9.5 0 0 1 1 2.5a1 1 0 0 1 1-1z"/></svg>
        <span>083-274-6159</span>
      </li>
      <li class="contact__item">
        <svg class="contact__icon" viewBox="0 0 12 12"><rect x="1" y="2.5" width="10" height="7"/><path d="M1 2.5l5 4 5-4"/></svg>
        <span>tobias@velmontestates.asia</span>
      </li>
      <li class="contact__item">
        <svg class="contact__icon" viewBox="0 0 12 12"><circle cx="6" cy="6" r="5"/><ellipse cx="6" cy="6" rx="2.2" ry="5"/><path d="M1 6h10"/></svg>
        <span>www.<span class="contact__domain">velmontestates.asia</span></span>
      </li>
      <li class="contact__item">
        <svg class="contact__icon" viewBox="0 0 12 12"><circle cx="6" cy="6" r="5"/><ellipse cx="6" cy="6" rx="2.2" ry="5"/><path d="M1 6h10"/></svg>
        <span>www.<span class="contact__domain">velmontestates.co.uk</span></span>
      </li>
    </ul>

    <div class="person">
      <p class="person__name">Tobias Hennlund</p>
      <p class="person__role">Managing Director</p>
    </div>
  </section>
</body>
</html>
```